Kestal-Materials. Limestone; improving the world

New Limestone company and need logo design.
Limestone offsets carbon mitigation industries restore and replenish soil fertilities in the Prairies, the breadbasket of the world. At the same time, Limestone is proving a critical emergent component of carbon capture sequestration technology will therefore play a critical role in the development of the western Canadian energy industries
Our limestone resources are situated in the foothills of the Canadian Rockies well-positioned above the sprawling fields of the vast peace district.
Agriculture and oli sites
Kestal Materials
3 page

```html
<!DOCTYPE html>
<html lang="en">
<head>
<meta charset="utf-8">
<title>Kestal Materials</title>
<link href="https://fonts.googleapis.com/css2?family=Roboto:wght@400;500;700&family=Rubik:wght@500;700&display=swap" rel="stylesheet">
<style>
:root{
  --blue:#3a9fd6;
  --steel:#4f6f87;
  --footer:#5a7992;
  --ink:#111;
  --muted:#777;
  --grey:#eef0f1;
  --white:#fff;
}
*{box-sizing:border-box;margin:0;padding:0}
html,body{width:1200px;height:4134px;overflow:hidden}
body{font-family:Roboto,Arial,sans-serif;color:var(--ink);background:var(--white);position:relative}
.abs{position:absolute}
.topbar{top:0;left:0;width:1200px;height:43px;background:var(--blue);color:#fff;font-size:13px}
.topbar span{position:absolute;top:13px}
.nav{top:43px;left:0;width:1200px;height:69px;background:#fff;border-bottom:1px solid #e5e5e5}
.brand{position:absolute;left:100px;top:14px;width:140px;text-align:center;font-family:Rubik,sans-serif;font-weight:700;font-size:12px;color:#1a2a4a}
.brand i{display:block;width:26px;height:22px;background:var(--blue);margin:0 auto 6px}
.menu{position:absolute;left:328px;top:27px;display:flex;gap:17px;font-family:Rubik,sans-serif;font-weight:500;font-size:13px;color:#111}
.menu .on{color:var(--blue)}
.portal{position:absolute;left:946px;top:12px;width:155px;height:44px;background:var(--steel);color:#fff;font-family:Rubik,sans-serif;font-weight:500;font-size:13px;display:flex;align-items:center;justify-content:center;border-radius:2px}
.hero{top:112px;left:0;width:1200px;height:552px;background:linear-gradient(180deg,#c9d6de 0%,#8f9791 30%,#4f5b3b 48%,#6d7b6a 62%,#3e4a38 100%)}
.hero h1{position:absolute;top:246px;width:100%;text-align:center;font-family:Rubik,sans-serif;font-weight:700;font-size:40px;color:#fff}
.hero p{position:absolute;top:310px;width:100%;text-align:center;font-family:Rubik,sans-serif;font-weight:500;font-size:20px;color:#fff}
.dots{position:absolute;top:502px;left:572px;display:flex;gap:3px}
.dots b{width:9px;height:9px;border-radius:50%;background:#fff}
.dots b.o{background:transparent;border:2px solid #fff}
.kicker{width:100%;text-align:center;font-family:Rubik,sans-serif;font-weight:500;font-size:13px;color:var(--blue)}
.title{width:100%;text-align:center;font-family:Rubik,sans-serif;font-weight:700;font-size:35px;color:var(--ink)}
.rule{width:34px;height:2px;background:var(--blue)}
.card{width:311px;height:272px;border:5px solid #fff;box-shadow:0 0 6px rgba(0,0,0,.18);border-radius:4px;overflow:hidden}
.card .ph{width:100%;height:100%}
.card h3{position:absolute;left:35px;top:178px;font-family:Rubik,sans-serif;font-weight:700;font-size:19px;color:#fff}
.card p{position:absolute;left:35px;top:210px;font-size:14px;color:#fff}
.about{top:1606px;left:0;width:1200px;height:523px;background:linear-gradient(180deg,#eceeef,#e3e7e9)}
.about .kick{position:absolute;left:110px;top:78px;font-family:Rubik,sans-serif;font-weight:500;font-size:13px;color:var(--blue)}
.about h2{position:absolute;left:110px;top:106px;font-family:Rubik,sans-serif;font-weight:700;font-size:35px}
.about .rule{position:absolute;left:110px;top:160px}
.about .copy{position:absolute;left:110px;top:185px;width:420px;font-size:14px;line-height:26px;color:var(--muted)}
.btn{background:var(--steel);color:#fff;font-family:Rubik,sans-serif;font-weight:500;font-size:14px;display:flex;align-items:center;justify-content:center;gap:10px;border-radius:2px}
.about .btn{position:absolute;left:110px;top:392px;width:175px;height:50px}
.video{left:614px;top:93px;width:475px;height:338px;background:linear-gradient(135deg,#3c5470,#8a8f8c 50%,#cfcfc9)}
.play{position:absolute;left:207px;top:140px;width:60px;height:60px;border-radius:50%;background:#fff;display:flex;align-items:center;justify-content:center}
.feat{width:237px;height:270px;background:#fff;box-shadow:0 0 6px rgba(0,0,0,.15);text-align:center}
.feat svg{margin-top:18px}
.feat h4{margin-top:20px;font-family:Rubik,sans-serif;font-weight:500;font-size:14px}
.feat .rule{margin:14px auto 0;width:28px}
.feat p{margin:13px 24px 0;font-size:13px;line-height:21px;color:var(--muted)}
.feat a{display:inline-block;margin-top:12px;font-size:12px;font-weight:700;color:var(--blue);text-decoration:underline}
.sustain{top:2764px;left:0;width:1200px;height:390px;background:linear-gradient(180deg,#e6eef2 0%,#d6e0d6 40%,#a6b98a 75%,#7a9866 100%)}
.sustain h2{position:absolute;top:68px;width:100%;text-align:center;font-family:Rubik,sans-serif;font-weight:700;font-size:30px}
.sustain p{position:absolute;top:130px;left:228px;width:744px;text-align:center;font-size:14px;line-height:26px;color:#6a6a6a}
.sustain .btn{position:absolute;left:447px;top:262px;width:310px;height:50px}
.gal{height:225px;width:237px}
.footer{top:3755px;left:0;width:1200px;height:379px;background:var(--footer);color:#fff;font-size:14px}
.footer h5{position:absolute;top:66px;font-family:Rubik,sans-serif;font-weight:500;font-size:14px;text-decoration:underline}
.footer ul{position:absolute;top:100px;list-style:none;line-height:34px}
.footer li::before{content:"»";margin-right:14px}
.ci{position:absolute;left:550px;width:32px;height:32px;border-radius:50%;background:#fff;display:flex;align-items:center;justify-content:center}
.ctext{position:absolute;left:598px;font-size:13px;line-height:22px}
.email{position:absolute;left:818px;top:167px;width:272px;height:48px;background:#fff;color:#888;font-size:13px;display:flex;align-items:center;padding-left:22px}
.sub{position:absolute;left:818px;top:226px;width:148px;height:50px;background:var(--blue)}
.fline{position:absolute;left:110px;top:320px;width:980px;height:1px;background:rgba(255,255,255,.5)}
.copyr{position:absolute;left:110px;top:339px;font-size:13px}
.soc{position:absolute;top:339px;width:14px;height:14px;border-radius:50%;background:#fff}
</style>
</head>
<body>
<div class="abs topbar">
  <span style="left:118px">✉&nbsp;&nbsp;&nbsp;hello@kestalmaterials.com</span>
  <span style="left:795px">✆&nbsp;&nbsp;&nbsp;&nbsp;1 800 555 0142</span>
  <span style="left:967px;font-weight:700">ENG &nbsp;⌄</span>
  <span style="left:1050px">⌕</span>
</div>
<header class="abs nav">
  <div class="brand"><i></i>KESTAL MATERIALS</div>
  <nav class="menu"><span class="on">HOME</span><span>PRODUCTS</span><span>MARKETS</span><span>LOCATIONS</span><span>SUSTAINABILITY</span><span>ABOUT US</span><span>CAREERS</span></nav>
  <div class="portal">CUSTOMER PORTAL</div>
</header>
<section class="abs hero" role="img" aria-label="Mountain range with forest reflected in a still lake">
  <h1>STUNNING . NATURAL . CANADIAN</h1>
  <p>BE STRONGER TOGETHER</p>
  <div class="dots"><b></b><b></b><b class="o"></b><b></b><b></b></div>
</section>

<div class="abs kicker" style="top:765px">OUR BUSINESS CUSTOMERS</div>
<h2 class="abs title" style="top:792px">WHO WE SERVE</h2>
<div class="abs rule" style="left:583px;top:848px"></div>

<div class="abs card" style="left:107px;top:899px"><div class="ph" role="img" aria-label="Pile of crushed limestone in a field" style="background:linear-gradient(180deg,#8ba8c6,#b4b4ae 55%,#5d5044)"></div><h3>INSTALLER</h3><p>Lorem ipsum dolor sit amet, consec</p></div>
<div class="abs card" style="left:442px;top:899px"><div class="ph" role="img" aria-label="Open limestone quarry under a cloudy sky" style="background:linear-gradient(180deg,#4a5868,#8f8a80 45%,#a9a59c)"></div><h3>CABINET SHOPS</h3><p>Lorem ipsum dolor sit amet, consec</p></div>
<div class="abs card" style="left:777px;top:899px"><div class="ph" role="img" aria-label="Stone staircase in a bright interior" style="background:linear-gradient(135deg,#8b6a4c,#cfc7bd 50%,#8f8f8d)"></div><h3>BUILDER</h3><p>Lorem ipsum dolor sit amet, consec</p></div>
<div class="abs card" style="left:107px;top:1199px"><div class="ph" role="img" aria-label="Excavator working on a rock pile" style="background:linear-gradient(180deg,#8fb2d6,#a6a29a 55%,#6a6158)"></div><h3>CONTRACTORS</h3><p>Lorem ipsum dolor sit amet, consec</p></div>
<div class="abs card" style="left:442px;top:1199px"><div class="ph" role="img" aria-label="Excavator on quarry boulders" style="background:linear-gradient(180deg,#5f8cc0,#b9b5ab 55%,#6e6559)"></div><h3>DEVELOPERS</h3><p>Lorem ipsum dolor sit amet, consec</p></div>
<div class="abs card" style="left:777px;top:1199px"><div class="ph" role="img" aria-label="Bright white kitchen interior" style="background:linear-gradient(180deg,#d8d6d2,#b9b4ad 60%,#6f665e)"></div><h3>INTERIOR DESIGNERS</h3><p>Lorem ipsum dolor sit amet, consec</p></div>

<section class="abs about">
  <div class="kick">WHO WE ARE</div>
  <h2>ABOUT US</h2>
  <div class="rule"></div>
  <p class="copy">Lorem ipsum dolor sit amet, consectetur adipiscing elit, sed do eiusmod tempor incididunt ut labore et dolore magna aliqua. Ut enim ad minim veniam, quis nostrud exercitation ullamco laboris nisi ut aliquip ex ea commodo consequat. Duis aute irure dolor in reprehenderit in voluptate velit esse cillum dolore eu fugiat nulla pariatur. Excepteur sint occaecat cupidatat non proident, sunt in culpa qui officia deserunt mollit anim id est laborum.</p>
  <div class="btn">DISCOVER NOW <svg width="13" height="13" viewBox="0 0 14 14"><circle cx="7" cy="7" r="7" fill="#fff"/><path d="M5 4l4 3-4 3" stroke="#4f6f87" stroke-width="2" fill="none"/></svg></div>
  <div class="abs video" role="img" aria-label="Mining trucks and excavator moving stone in a dusty quarry">
    <div class="play"><svg width="30" height="30" viewBox="0 0 30 30"><circle cx="15" cy="15" r="15" fill="#3a9fd6"/><path d="M11 8l11 7-11 7z" fill="#fff"/></svg></div>
  </div>
</section>

<div class="abs kicker" style="top:2239px">OUR ADVANTAGES</div>
<h2 class="abs title" style="top:2266px">WHY CHOOSE US</h2>
<div class="abs rule" style="left:583px;top:2321px"></div>

<div class="abs feat" style="left:103px;top:2382px">
  <svg width="56" height="56" viewBox="0 0 56 56"><path d="M28 4L50 16V40L28 52L6 40V16Z" fill="none" stroke="#3a9fd6" stroke-width="5"/><path d="M28 4V52M6 16L50 40M50 16L6 40" stroke="#3a9fd6" stroke-width="3"/></svg>
  <h4>LOTS OF CHOICES</h4><div class="rule"></div>
  <p>Lorem ipsum dolor sit amet, consectetur adipiscing elit, sed do eiusmod tempor incidid</p>
  <a>LEARN MORE ➜</a>
</div>
<div class="abs feat" style="left:355px;top:2382px">
  <svg width="56" height="56" viewBox="0 0 56 56"><path d="M30 6H50V26L24 52L4 32Z" fill="#3a9fd6"/><circle cx="41" cy="15" r="4" fill="#fff"/></svg>
  <h4>AFFORDABLE PRICES</h4><div class="rule"></div>
  <p>Lorem ipsum dolor sit amet, consectetur adipiscing elit, sed do eiusmod tempor incidid</p>
  <a>LEARN MORE ➜</a>
</div>
<div class="abs feat" style="left:608px;top:2382px">
  <svg width="56" height="56" viewBox="0 0 56 56"><path d="M28 4C18 4 11 11 11 20C11 32 28 52 28 52S45 32 45 20C45 11 38 4 28 4Z" fill="#3a9fd6"/><circle cx="28" cy="20" r="6" fill="#fff"/></svg>
  <h4>CONVENIENT LOCATION</h4><div class="rule"></div>
  <p>Lorem ipsum dolor sit amet, consectetur adipiscing elit, sed do eiusmod tempor incidid</p>
  <a>LEARN MORE ➜</a>
</div>
<div class="abs feat" style="left:860px;top:2382px">
  <svg width="56" height="56" viewBox="0 0 56 56"><circle cx="22" cy="16" r="9" fill="#3a9fd6"/><path d="M6 50C6 36 14 30 22 30S38 36 38 50Z" fill="#3a9fd6"/><circle cx="42" cy="34" r="8" fill="none" stroke="#3a9fd6" stroke-width="4"/></svg>
  <h4>GREAT CONSULTANTS</h4><div class="rule"></div>
  <p>Lorem ipsum dolor sit amet, consectetur adipiscing elit, sed do eiusmod tempor incidid</p>
  <a>LEARN MORE ➜</a>
</div>

<section class="abs sustain" role="img" aria-label="Misty green forested hills">
  <h2>SUSTAINABILITY</h2>
  <p>Sed ut perspiciatis unde omnis iste natus error sit voluptatem accusantium doloremque laudantium, totam rem aperiam, eaque ipsa quae ab illo inventore veritatis et quasi architecto beatae vitae dicta sunt explicabo. Nemo enim ipsam voluptatem quia voluptas sit aspernatur aut odit aut fugit, sed quia consequuntur magni dolores eos qui ratione voluptatem sequi nesciunt.</p>
  <div class="btn">DOWNLOAD SUSTAINABILITY REPORT <svg width="13" height="13" viewBox="0 0 14 14"><circle cx="7" cy="7" r="7" fill="#fff"/><path d="M5 4l4 3-4 3" stroke="#4f6f87" stroke-width="2" fill="none"/></svg></div>
</section>

<div class="abs kicker" style="top:3255px">RECENT PROJECTS</div>
<h2 class="abs title" style="top:3281px">OUR GALLERY</h2>
<div class="abs rule" style="left:583px;top:3336px"></div>
<div class="abs gal" style="left:111px;top:3386px;background:linear-gradient(180deg,#4a4036,#7fb6d8 45%,#d8c9a6)" role="img" aria-label="Sea cave opening onto a tropical beach"></div>
<div class="abs gal" style="left:358px;top:3386px;background:radial-gradient(circle at 50% 45%,#b9c3c8,#3a3632 45%,#1d1b19)" role="img" aria-label="Dark rock cave looking out to light"></div>
<div class="abs gal" style="left:603px;top:3386px;background:linear-gradient(180deg,#c9a56a,#9a8f7b 50%,#6a6256)" role="img" aria-label="Limestone pavement with a lone tree at sunset"></div>
<div class="abs gal" style="left:850px;top:3386px;background:radial-gradient(circle at 50% 55%,#3a2a1f,#8c6f55 40%,#c9b49e)" role="img" aria-label="Tunnel carved into sandy stone"></div>

<footer class="abs footer">
  <h5 style="left:110px">QUICK LINKS</h5>
  <ul style="left:110px"><li>Home</li><li>About Us</li><li>Services</li><li>Contact Us</li><li>Stones</li></ul>
  <h5 style="left:325px">OTHER LINKS</h5>
  <ul style="left:325px"><li>FAQ</li><li>Help Service</li><li>Terms Of Use</li><li>Privacy Policy</li><li>Clients</li></ul>
  <h5 style="left:550px">CONTACT US</h5>
  <div class="ci" style="top:100px"><svg width="14" height="16" viewBox="0 0 14 16"><path d="M7 0C3 0 1 3 1 6c0 4 6 10 6 10s6-6 6-10c0-3-2-6-6-6z" fill="#5a7992"/><circle cx="7" cy="6" r="2" fill="#fff"/></svg></div>
  <div class="ctext" style="top:98px">214 Ridge Road<br>United States</div>
  <div class="ci" style="top:155px"><svg width="14" height="14" viewBox="0 0 14 14"><path d="M3 0l3 3-2 2c1 2 3 4 5 5l2-2 3 3-2 3C6 14 0 8 0 3z" fill="#5a7992"/></svg></div>
  <div class="ctext" style="top:160px">1 800 555 0142</div>
  <div class="ci" style="top:213px"><svg width="14" height="10" viewBox="0 0 14 10"><rect x="0.5" y="0.5" width="13" height="9" fill="none" stroke="#5a7992"/><path d="M1 1l6 5 6-5" stroke="#5a7992" fill="none"/></svg></div>
  <div class="ctext" style="top:218px">hello@kestalmaterials.com</div>
  <h5 style="left:818px">NEWSLETTER</h5>
  <p class="abs" style="left:818px;top:100px;width:280px;line-height:24px">At vero eos et accusamus et iusto odio dignissimos ducimus qui blanditiis.</p>
  <div class="email">✉&nbsp;&nbsp; Email Address</div>
  <div class="btn sub">SUBSCRIBE <svg width="13" height="13" viewBox="0 0 14 14"><circle cx="7" cy="7" r="7" fill="#fff"/><path d="M5 4l4 3-4 3" stroke="#3a9fd6" stroke-width="2" fill="none"/></svg></div>
  <div class="fline"></div>
  <div class="copyr">© 2021 Kestal Materials. All Rights Reserved</div>
  <span class="soc" style="left:980px"></span><span class="soc" style="left:1008px"></span><span class="soc" style="left:1036px"></span><span class="soc" style="left:1064px"></span>
</footer>
</body>
</html>
```